Brenwick Structures Construction Company Seeking Modern Website

We are a small construction company wanting to create a web presence. We don't have much in the way of current content but will get photos as they come in. Attached is a picture of our business card.
The pages we would like on the menu are:
Home
Portfolio
Product Specs
Testimonials
Our Process
Contact
Some designs we like are:
http://www.tovasheds-example.com/
http://www.qrnstructures-example.com/
http://dunholtbarns-example.com/
http://pellingframes-example.com/
Not much requirements other than that so feel free to be creative!
Updates
Target Market(s)
Construction
Commercial and Residential Buildings
Industry/Entity Type
Construction Company
Number of Pages Required
5+ page
Look and feel

```html
<!DOCTYPE html>
<html lang="en">
<head>
<meta charset="utf-8">
<title>Brenwick Structures</title>
<link rel="stylesheet" href="https://fonts.googleapis.com/css2?family=Raleway:wght@400;500;600&family=Roboto:wght@300;400;500&display=swap">
<style>
:root{
  --page:#f4f4f4;--white:#fff;--ink:#333;--muted:#8a8a8a;--red:#d9312b;--blue:#0c9fde;
  --teal:#2b6d8c;--dark:#211f20;--darker:#141414;--line:#e3e3e3;--grey-tab:#dcdcdc;
}
*{box-sizing:border-box;margin:0;padding:0}
html,body{width:1200px;height:2659px;overflow:hidden}
body{background:var(--page);font-family:"Roboto",sans-serif;color:var(--ink);position:relative}
.abs{position:absolute}
p{font-size:11.5px;line-height:1.75;color:var(--muted);font-weight:300}
.readmore{font-size:12.5px;color:var(--red)}
h3{font-family:"Raleway",sans-serif;font-weight:500;font-size:15px;color:#444}

.header{left:0;top:0;width:1200px;height:127px}
.brand{left:124px;top:46px;display:flex;align-items:center;gap:10px;font-family:"Raleway",sans-serif;font-weight:600;font-size:26px;color:var(--red)}
.brand i{width:14px;height:14px;background:var(--blue);display:block}
.nav{right:126px;top:58px;display:flex;gap:44px;font-size:12px;color:#555}
.nav .active{color:var(--red)}

.hero{left:124px;top:127px;width:950px;height:448px;background:linear-gradient(160deg,#b9a58a 0%,#8f8775 35%,#4d4a44 70%,#2e2d2b 100%)}
.hero-text{left:159px;top:285px;font-family:"Raleway",sans-serif}
.hero-text h1{font-weight:400;font-size:45px;color:var(--red);line-height:1.1}
.hero-text h2{font-weight:500;font-size:28px;color:#fff;line-height:1.45;margin-top:10px}
.hero-dots{left:484px;top:394px;display:flex;gap:4px}
.hero-dots span{width:18px;height:18px;border-radius:50%;border:1px solid #fff;background:rgba(255,255,255,.35)}

.cta{left:124px;top:575px;width:950px;height:83px;background:var(--blue);color:#fff;font-family:"Raleway",sans-serif}
.cta-line{left:62px;top:30px;font-size:18px}
.cta-btn{left:716px;top:24px;width:176px;height:37px;border:1.5px solid #fff;text-align:center;line-height:34px;font-size:17px}

.features{left:124px;top:658px;width:950px;height:452px;background:var(--white)}
.photo{display:block}
.feature h3{margin-bottom:10px}

.tabs-sec{left:124px;top:1110px;width:950px;height:463px}
.tab{top:67px;height:41px;line-height:41px;font-family:"Raleway",sans-serif;font-size:14px}
.tab-a{left:37px;width:260px;background:var(--blue);color:#fff;padding-left:30px;clip-path:polygon(0 0,225px 0,260px 100%,0 100%)}
.tab-b{left:258px;width:302px;background:var(--grey-tab);color:#555;padding-left:66px;clip-path:polygon(0 0,267px 0,302px 100%,35px 100%)}
.card{left:37px;top:143px;width:602px;height:243px;background:#fff;border:1px solid var(--line)}
.points{left:690px;top:143px}
.point{display:flex;align-items:center;gap:24px;height:92px;font-family:"Raleway",sans-serif;font-size:18px;color:#555}
.point .ico{width:62px;height:62px;border-radius:50%;background:var(--red);border:3px solid #7d1410;display:flex;align-items:center;justify-content:center}

.projects{left:124px;top:1573px;width:950px;height:409px;background:linear-gradient(135deg,#2f7595,#245f7c)}
.projects h2{left:35px;top:50px;font-family:"Raleway",sans-serif;font-weight:400;font-size:22px;color:#fff}
.filters{left:329px;top:42px;width:582px;height:42px;border-top:1px solid rgba(255,255,255,.5);border-bottom:1px solid rgba(255,255,255,.5);display:flex;justify-content:space-around;align-items:center;font-size:11.5px;color:#d8e6ee}
.filters .on{color:#fff}
.shot{top:137px;width:209px;height:214px}
.side-arrow{width:16px;height:16px;border-radius:50%;border:1px solid rgba(255,255,255,.6)}

.testi{left:124px;top:1982px;width:950px;height:358px;background:#fafafa}
.testi h2{left:35px;top:56px;font-family:"Raleway",sans-serif;font-weight:400;font-size:22px;color:#333}
.quote{top:110px;width:419px;height:149px;background:#fff;border:1px solid var(--line);padding:14px 26px}
.quote p{font-size:11.5px;text-align:justify}
.quote .by{position:absolute;left:132px;top:113px;font-size:12px;color:#444}
.avatar{top:220px;width:78px;height:78px;border-radius:50%;border:2px solid #ccc;background:linear-gradient(#b9b4ad,#7c766f)}

.footer{left:124px;top:2340px;width:950px;height:265px;background:var(--dark);color:#fff}
.footer h4{font-family:"Raleway",sans-serif;font-weight:400;font-size:22px;margin-bottom:20px}
.footer p{color:#8d8d8d;font-size:11px;line-height:1.8}
.contact-row{display:flex;gap:18px;margin-bottom:12px;align-items:flex-start}
.social{display:flex;gap:7px;margin-top:14px}
.social span{width:18px;height:18px;border-radius:50%}
.field{width:200px;border-bottom:1px solid #444;font-size:11px;color:#666;padding-bottom:8px;margin-top:12px;font-style:italic}
.send{margin-top:16px;width:86px;height:28px;background:var(--red);text-align:center;line-height:28px;font-size:13px}
.copy{left:124px;top:2605px;width:950px;height:54px;background:var(--darker);color:#ddd;font-size:11.5px}
</style>
</head>
<body>

<header class="header abs">
  <div class="brand abs"><i></i>Brenwick Structures</div>
  <nav class="nav abs"><span class="active">Home</span><span>Portfolio</span><span>Product Specs</span><span>Testimonials</span><span>Our Process</span><span>Contact</span></nav>
</header>

<section class="hero abs" role="img" aria-label="Cranes over high-rise buildings under construction against a cloudy sky"></section>
<div class="hero-text abs">
  <h1>Brenwick Structures</h1>
  <h2>Buliding Dreams, So You<br>Can Build Memories</h2>
</div>
<div class="hero-dots abs"><span></span><span></span></div>

<section class="cta abs">
  <div class="cta-line abs">We are the Expert on this Field, Better construction Since The Year</div>
  <div class="cta-btn abs">Conatct Us</div>
</section>

<section class="features abs">
  <div class="feature abs" style="left:37px;top:66px;width:273px">
    <div class="photo" role="img" aria-label="Steel frame of a building with a crane under blue sky" style="height:160px;background:linear-gradient(#7eb3d8,#c9b79b)"></div>
    <h3 style="margin-top:26px">Harlan Whitcombe</h3>
    <p>There are many variations of passages of Lorem Ipsum available, but the majority have suffered alteration in some form, by injected humour, or randomised words which don't look even slightly believable.</p>
    <div class="readmore" style="margin-top:12px">Read More</div>
  </div>
  <div class="feature abs" style="left:338px;top:66px;width:273px">
    <h3>Bonorum et Malorum</h3>
    <p>There are many variations of passages of Lorem Ipsum available, but the majority have suffered alteration in some form, by injected humour, or randomised words which don't look even slightly believable.</p>
    <div class="readmore" style="margin-top:12px">Read More</div>
    <div class="photo" role="img" aria-label="Excavator working on a snowy site" style="height:160px;margin-top:22px;background:linear-gradient(135deg,#2a3646,#6d7f92 60%,#c9a24a)"></div>
  </div>
  <div class="feature abs" style="left:639px;top:66px;width:273px">
    <div class="photo" role="img" aria-label="Workers and rebar silhouetted at sunset" style="height:160px;background:linear-gradient(#4a5f7a,#d98a3a 70%,#2b2218)"></div>
    <h3 style="margin-top:26px">Corporis Suscipit</h3>
    <p>There are many variations of passages of Lorem Ipsum available, but the majority have suffered alteration in some form, by injected humour, or randomised words which don't look even slightly believable.</p>
    <div class="readmore" style="margin-top:12px">Read More</div>
  </div>
</section>

<section class="tabs-sec abs">
  <div class="tab tab-b abs">Residential Buildings</div>
  <div class="tab tab-a abs">Commercial Construction</div>
  <div class="card abs">
    <div class="abs" role="img" aria-label="Tower cranes beside a glass office tower at sunset" style="left:0;top:0;width:292px;height:241px;background:linear-gradient(160deg,#e8c48a,#8d8a86 55%,#3e4a58)"></div>
    <div class="abs" style="left:290px;top:34px;width:275px">
      <h3>Commercial Construction</h3>
      <p style="margin-top:12px;text-align:justify">Many desktop publishing packages and web page editors now use Lorem Ipsum as their default model text, and a search for 'lorem ipsum' will uncover many web sites still in their infancy. Various versions have evolved over the years, sometimes by accident, sometimes on purpose</p>
      <div class="readmore" style="margin-top:14px">Read More</div>
    </div>
  </div>
  <div class="points abs">
    <div class="point"><span class="ico"><svg width="26" height="22" viewBox="0 0 26 22" fill="none" stroke="#fff" stroke-width="2"><rect x="4" y="2" width="18" height="13"/><path d="M1 19h24"/></svg></span>Good Planning</div>
    <div class="point"><span class="ico"><svg width="28" height="24" viewBox="0 0 28 24" fill="#fff"><circle cx="14" cy="6" r="4"/><circle cx="6" cy="9" r="3"/><circle cx="22" cy="9" r="3"/><path d="M7 22c0-6 3-9 7-9s7 3 7 9z"/><path d="M0 22c0-5 2-8 6-8 1 0 2 0 3 1-2 2-3 4-3 7z"/><path d="M28 22c0-5-2-8-6-8-1 0-2 0-3 1 2 2 3 4 3 7z"/></svg></span>Awesome Stuff</div>
    <div class="point"><span class="ico"><svg width="20" height="26" viewBox="0 0 20 26" fill="none" stroke="#fff" stroke-width="2"><rect x="2" y="1" width="16" height="24"/><path d="M6 6h2M12 6h2M6 11h2M12 11h2M6 16h2M12 16h2M8 25v-5h4v5"/></svg></span>Construction</div>
  </div>
</section>

<section class="projects abs">
  <h2 class="abs">Recent Projects</h2>
  <div class="filters abs"><span class="on">All Projects</span><span>Design</span><span>Buildings</span><span>Constructions</span><span>Isolations</span></div>
  <div class="side-arrow abs" style="left:10px;top:238px"></div>
  <div class="side-arrow abs" style="left:921px;top:238px"></div>
  <div class="shot abs" role="img" aria-label="Scaffolding in bright sunlight" style="left:37px;background:linear-gradient(160deg,#f3dcc0,#c7d3e1 50%,#8aa1ba)"></div>
  <div class="abs" style="left:208px;top:137px;width:38px;height:38px;background:#4aa8d8"></div>
  <div class="abs" style="left:208px;top:175px;width:38px;height:38px;background:#6cc0e8"></div>
  <div class="shot abs" role="img" aria-label="Concrete building frame under construction" style="left:260px;background:linear-gradient(#6c9fd6,#b9b2a6 55%,#7c7367)"></div>
  <div class="shot abs" role="img" aria-label="Glass skyscraper seen from below" style="left:481px;background:linear-gradient(135deg,#cfe3f2,#4b87b3 50%,#1d3a57)"></div>
  <div class="shot abs" role="img" aria-label="Modern glass office building at dusk" style="left:703px;background:linear-gradient(#2c4f9a,#3f5ea8 45%,#7b6a6e 75%,#3b3b3b)"></div>
</section>

<section class="testi abs">
  <h2 class="abs">Testimonial</h2>
  <div class="abs" style="left:10px;top:158px;width:16px;height:16px;border-radius:50%;border:1px solid #ccc"></div>
  <div class="abs" style="left:924px;top:158px;width:16px;height:16px;border-radius:50%;border:1px solid #ccc"></div>
  <div class="quote abs" style="left:37px">
    <p>"Lorem Ipsum is not simply random text. It has roots in a piece of classical Latin literature from 45 BC, making it over 2000 years old. Harlan Whitcombe, a Latin professor at Ashgrove College in Vermont, looked up one of the more obscure Latin words"</p>
    <span class="by">- Bonorum et Malorum</span>
  </div>
  <div class="avatar abs" role="img" aria-label="Portrait of a client" style="left:67px"></div>
  <div class="quote abs" style="left:494px">
    <p>"Lorem Ipsum is not simply random text. It has roots in a piece of classical Latin literature from 45 BC, making it over 2000 years old. Harlan Whitcombe, a Latin professor at Ashgrove College in Vermont, looked up one of the more obscure Latin words"</p>
    <span class="by">- Bonorum et Malorum</span>
  </div>
  <div class="avatar abs" role="img" aria-label="Portrait of a client" style="left:524px"></div>
</section>

<footer class="footer abs">
  <div class="abs" style="left:39px;top:46px;width:300px">
    <h4>About us</h4>
    <p style="text-align:justify">a Latin professor at Ashgrove College in Vermont, looked up one of the more obscure Latin words, consectetur, from a Lorem Ipsum passage, and going through the cites of the word in classical literature, discovered the undoubtable source. Lorem Ipsum comes from sections</p>
    <div class="social"><span style="background:#2fa9e0"></span><span style="background:#f09a28"></span><span style="background:#3b5a9a"></span><span style="background:#d2453b"></span><span style="background:#666"></span></div>
  </div>
  <div class="abs" style="left:398px;top:46px;width:240px">
    <h4>Get In Touch</h4>
    <div class="contact-row"><svg width="10" height="14" viewBox="0 0 10 14"><path d="M5 0a5 5 0 0 0-5 5c0 4 5 9 5 9s5-5 5-9a5 5 0 0 0-5-5zm0 7a2 2 0 1 1 0-4 2 2 0 0 1 0 4z" fill="#d9312b"/></svg><p>200 Latin words, combined with a handful of model sentence structures</p></div>
    <div class="contact-row"><svg width="12" height="12" viewBox="0 0 12 12"><path d="M2 0l2 3-1 1.5c1 2 2.5 3.5 4.5 4.5L9 8l3 2-1 2C5 12 0 7 0 1z" fill="#d9312b"/></svg><p>5550142871 / 5550193364</p></div>
    <div class="contact-row"><svg width="13" height="10" viewBox="0 0 13 10" fill="none" stroke="#d9312b" stroke-width="1.5"><rect x="1" y="1" width="11" height="8"/><path d="M1 1l5.5 4L12 1"/></svg><p>info@brenwickstructures-example.com</p></div>
  </div>
  <div class="abs" style="left:697px;top:46px;width:220px">
    <h4>Newsletter</h4>
    <p>Subscribe to Newsletters for more information and updates</p>
    <div class="field">Email id</div>
    <div class="send">Send Now</div>
  </div>
</footer>
<div class="copy abs"><span class="abs" style="left:37px;top:20px">Copyrights@Brenwick Structures2015</span><span class="abs" style="right:18px;top:20px">C15</span></div>

</body>
</html>
```